Quorva - corporate Business Card

We need a good look and innovative business card for a new start up company based in Los Angeles called "Quorva". We are in a payment business, including payment card, app, and ewallet. We are expert in online payment and Card not present (CNP) transaction.
We need an innovative, modern business card.

Our logo font is Aero Matics

Target Market(s)

Startup - Bank - Online Payment - Card Manufacturing

Industry/Entity Type

Startup

Contact Information for Business Card

phone: 555 014 7396 - Address: 4172 Marlowe blvd, Norvale Heights, CA 90299

Requirements
Must have
• Message: innovative, professional, expert, high tech, trust, online payment expert, security
Nice to have
• no comment
Should not have
• no Comment

```html
<!DOCTYPE html>
<html lang="en">
<head>
<meta charset="UTF-8">
<title>Quorva – Business Card</title>
<link rel="stylesheet" href="https://fonts.googleapis.com/css2?family=Lato:wght@400;700;900&display=swap">
<style>
  :root {
    --brand-red: #b81f2e;
    --ink: #2b2b2b;
    --paper: #ffffff;
    --edge-grey: #8d8d8d;
    --backdrop: #5f6a70;
  }
  * { margin: 0; padding: 0; box-sizing: border-box; }
  html, body { width: 1200px; height: 900px; overflow: hidden; }
  body {
    background: var(--backdrop);
    font-family: "Lato", Arial, sans-serif;
    position: relative;
  }
  .card {
    position: absolute;
    left: 280px;
    width: 640px;
    height: 366px;
    overflow: hidden;
    box-shadow: 0 10px 30px rgba(0,0,0,.35);
  }

  /* Front side */
  .card--front { top: 54px; background: var(--brand-red); color: var(--paper); }
  .front-mark {
    position: absolute; left: 96px; top: 108px;
    display: flex; align-items: center; gap: 22px;
  }
  .front-mark__dot { width: 128px; height: 128px; border-radius: 50%; background: var(--paper); flex: none; }
  .front-mark__name { font-weight: 900; font-size: 108px; letter-spacing: 2px; line-height: 1; }
  .front-web {
    position: absolute; left: 96px; bottom: 42px;
    font-size: 17px; letter-spacing: .5px;
  }

  /* Back side */
  .card--back { top: 480px; background: var(--paper); color: var(--ink); }
  .side-band { position: absolute; left: 0; top: 0; width: 90px; height: 366px; }
  .back-mark {
    position: absolute; left: 200px; top: 40px;
    display: flex; align-items: center; gap: 12px; color: var(--brand-red);
  }
  .back-mark__dot { width: 60px; height: 60px; border-radius: 50%; background: var(--brand-red); flex: none; }
  .back-mark__name { font-weight: 900; font-size: 54px; letter-spacing: 1px; line-height: 1; }
  .contact-list {
    position: absolute; left: 108px; top: 130px; list-style: none;
    font-size: 16px; line-height: 30px;
  }
  .person { position: absolute; right: 60px; top: 218px; text-align: right; }
  .person__name { color: var(--brand-red); font-size: 26px; font-weight: 400; letter-spacing: .5px; line-height: 1.1; }
  .person__role { font-size: 16px; }
  .address {
    position: absolute; right: 60px; top: 290px; text-align: right;
    font-size: 17px; line-height: 22px; font-style: normal;
  }
  .corner-tab { position: absolute; right: 0; top: 262px; width: 34px; height: 30px; background: var(--brand-red); }
</style>
</head>
<body>

<section class="card card--front" aria-label="Business card front">
  <div class="front-mark">
    <span class="front-mark__dot"></span>
    <span class="front-mark__name">quorva</span>
  </div>
  <p class="front-web">www.quorvapay.com</p>
</section>

<section class="card card--back" aria-label="Business card back">
  <svg class="side-band" viewBox="0 0 90 366" aria-hidden="true">
    <rect x="0" y="0" width="14" height="366" fill="var(--brand-red)"/>
    <polygon points="14,0 86,0 86,236 62,262 14,262" fill="var(--edge-grey)"/>
    <polygon points="14,0 78,0 78,232 56,254 14,254" fill="var(--brand-red)"/>
    <rect x="38" y="134" width="12" height="20" rx="2" fill="none" stroke="#fff" stroke-width="2"/>
    <path d="M38 168c0 8 6 14 14 14l2-4-4-3-2 2c-3-1-5-3-6-6l2-2-3-4z" fill="#fff"/>
    <rect x="36" y="196" width="18" height="12" fill="none" stroke="#fff" stroke-width="2"/>
    <path d="M36 196l9 7 9-7" fill="none" stroke="#fff" stroke-width="2"/>
    <circle cx="45" cy="234" r="9" fill="none" stroke="#fff" stroke-width="2"/>
    <path d="M36 234h18M45 225c-5 6-5 12 0 18M45 225c5 6 5 12 0 18" fill="none" stroke="#fff" stroke-width="1.5"/>
  </svg>

  <div class="back-mark">
    <span class="back-mark__dot"></span>
    <span class="back-mark__name">quorva</span>
  </div>

  <ul class="contact-list">
    <li>555 014 7396</li>
    <li>555 014 7396</li>
    <li>dana@quorvapay.com</li>
    <li>www.quorvapay.com</li>
  </ul>

  <div class="person">
    <p class="person__name">DANA REYES</p>
    <p class="person__role">Owner</p>
  </div>
  <span class="corner-tab"></span>

  <address class="address">
    4172 Marlowe blvd<br>Norvale Heights, CA 90299
  </address>
</section>

</body>
</html>
```